Business Card Design Project

Our slogan is "dare to be different" and we are after something creative and different to go with our company image.

Criteria:
The business card will not be a standard size but it must be small or big enough to fit in a wallet.
It will be double sided
It will have our colours and the design will be based around our logo (attached)
No fancy text just clean sharp easy to read. we have been using the stag sans book font type so this or similar type is preferable (we are not locked in a font type.

For more information about us, please visit out website at www.glimtrail.com.au

Target Market(s)

outdoor and recreational industry/market

Industry/Entity Type

Business

Requirements
Must have
• Logo
Slogan
website
contact details (phone and email)
Name and Position
social media facebook and youtube

```html
<!DOCTYPE html>
<html lang="en">
<head>
<meta charset="utf-8">
<title>Glimtrail Sports Australia – Business Card</title>
<link rel="stylesheet" href="https://fonts.googleapis.com/css2?family=Montserrat:wght@300;400;500&display=swap">
<style>
  :root {
    --stage: #d9d9d9;
    --card: #1f1f1f;
    --card-edge: #2a2a2a;
    --ring-faint: #2c2c2c;
    --orange: #f05a22;
    --white: #f2f2f2;
    --grey: #c9c9c9;
  }
  * { margin: 0; padding: 0; box-sizing: border-box; }
  html, body { width: 1200px; height: 900px; overflow: hidden; }
  body {
    background: var(--stage);
    font-family: "Montserrat", sans-serif;
    color: var(--white);
    position: relative;
  }
  .card {
    position: absolute;
    width: 760px;
    height: 400px;
    background: radial-gradient(ellipse at 60% 40%, var(--card-edge), var(--card) 70%);
    overflow: hidden;
    box-shadow: 0 10px 24px rgba(0,0,0,0.25);
  }
  .card::after {
    content: "";
    position: absolute;
    left: 0; right: 0; bottom: 0;
    height: 18px;
    background: var(--orange);
  }
  .card-back { left: 320px; top: 40px; }
  .card-front { left: 120px; top: 470px; }

  .faint-ring {
    position: absolute;
    width: 380px; height: 380px;
    border: 6px solid var(--ring-faint);
    border-radius: 50%;
  }
  .card-back .faint-ring { right: -110px; top: -150px; }
  .card-front .faint-ring { left: -190px; top: -10px; }

  /* Back */
  .brand-block {
    position: absolute;
    left: 0; right: 0; top: 56px;
    text-align: center;
  }
  .brand-dot {
    width: 140px; height: 140px;
    margin: 0 auto 18px;
    border: 5px solid var(--orange);
    border-radius: 50%;
  }
  .brand-name-back {
    font-weight: 400;
    font-size: 44px;
    letter-spacing: 3px;
    color: var(--white);
    line-height: 1;
  }
  .slogan {
    margin-top: 8px;
    font-size: 12px;
    font-weight: 500;
    letter-spacing: 3px;
    text-transform: uppercase;
    color: var(--white);
  }
  .website {
    position: absolute;
    left: 0; right: 0; bottom: 44px;
    text-align: center;
    font-size: 17px;
    letter-spacing: 1px;
    color: var(--orange);
  }

  /* Front */
  .brand-front {
    position: absolute;
    right: 60px; top: 70px;
    text-align: right;
  }
  .brand-name-front {
    font-weight: 300;
    font-size: 64px;
    letter-spacing: 4px;
    line-height: 1;
    color: var(--white);
  }
  .brand-sub {
    margin-top: 6px;
    font-size: 17px;
    letter-spacing: 4px;
    text-transform: uppercase;
    color: var(--orange);
  }
  .person {
    position: absolute;
    left: 50px; top: 222px;
  }
  .person-name {
    font-size: 26px;
    font-weight: 400;
    letter-spacing: 2px;
    text-transform: uppercase;
  }
  .person-role { font-size: 17px; color: var(--grey); margin-top: 2px; }
  .divider {
    position: absolute;
    left: 370px; top: 222px;
    width: 2px; height: 142px;
    background: var(--orange);
  }
  .contacts {
    position: absolute;
    left: 400px; top: 234px;
    list-style: none;
    font-size: 18px;
    line-height: 1.4;
  }
  .contacts li { display: flex; align-items: center; gap: 14px; }
  .contacts .label {
    width: 18px;
    color: var(--orange);
    font-size: 17px;
  }
  .contacts .social-dot {
    width: 18px; height: 18px;
    border-radius: 50%;
    background: var(--white);
  }
</style>
</head>
<body>
  <section class="card card-back" aria-label="Card back">
    <div class="faint-ring"></div>
    <div class="brand-block">
      <div class="brand-dot"></div>
      <div class="brand-name-back">GLIMTRAIL</div>
      <div class="slogan">Dare to be different</div>
    </div>
    <div class="website">www.glimtrail.com.au</div>
  </section>

  <section class="card card-front" aria-label="Card front">
    <div class="faint-ring"></div>
    <div class="brand-front">
      <div class="brand-name-front">GLIMTRAIL</div>
      <div class="brand-sub">Sports Australia</div>
    </div>
    <div class="person">
      <div class="person-name">Mara Lindqvist</div>
      <div class="person-role">Director</div>
    </div>
    <div class="divider"></div>
    <ul class="contacts">
      <li><span class="label">M</span><span>0400127364</span></li>
      <li><span class="label">E</span><span>enquiries@glimtrail.com.au</span></li>
      <li><span class="social-dot"></span><span>GlimtrailSports</span></li>
      <li><span class="social-dot"></span><span>TheGlimtrail</span></li>
    </ul>
  </section>
</body>
</html>
```